Business card for event manager / organizer "waiter service"

Draft of a new valuable business card for my company.
Events, personnel service providers, festivals

```html
<!DOCTYPE html>
<html lang="de">
<head>
<meta charset="utf-8">
<title>Leos Kellnerteam – Visitenkarte</title>
<link href="https://fonts.googleapis.com/css2?family=Oswald:wght@700&family=Questrial&display=swap" rel="stylesheet">
<style>
  :root {
    --bg: #dcdcdc;
    --card: #231f22;
    --orange: #e36a12;
    --white: #f4f4f4;
    --muted: #cfcfcf;
    --photo-light: #b9b9b9;
    --photo-dark: #2b2b2b;
  }
  * { margin: 0; padding: 0; box-sizing: border-box; }
  html, body { width: 1200px; height: 800px; overflow: hidden; }
  body {
    background: var(--bg);
    font-family: "Questrial", sans-serif;
    display: flex;
    align-items: center;
    justify-content: center;
    gap: 40px;
  }
  .card {
    width: 540px;
    height: 340px;
    background: var(--card);
    border-radius: 24px;
    overflow: hidden;
    position: relative;
    box-shadow: 0 3px 0 var(--orange), 0 14px 30px rgba(0,0,0,.25);
  }
  .card--front { display: flex; }
  .portrait {
    width: 235px;
    height: 100%;
    background: radial-gradient(ellipse at 60% 30%, var(--photo-light) 0%, #6e6e6e 45%, var(--photo-dark) 100%);
  }
  .details {
    flex: 1;
    padding: 26px 22px 20px 26px;
    color: var(--white);
  }
  .brand {
    display: flex;
    align-items: center;
    gap: 10px;
  }
  .brand__mark {
    width: 40px; height: 40px;
    background: var(--orange);
    flex: none;
  }
  .brand__name {
    font-family: "Oswald", sans-serif;
    font-weight: 700;
    color: var(--white);
    text-transform: uppercase;
    line-height: 1;
    font-size: 21px;
    letter-spacing: .5px;
  }
  .brand__tagline {
    font-size: 9px;
    color: var(--muted);
    margin-top: 4px;
  }
  .person__name {
    font-family: "Oswald", sans-serif;
    font-weight: 700;
    font-size: 22px;
    color: var(--orange);
    text-transform: uppercase;
    margin-top: 26px;
    letter-spacing: .5px;
  }
  .person__role { font-size: 15px; margin-top: 2px; }
  .address { font-size: 14px; margin-top: 14px; }
  .contacts { list-style: none; margin-top: 12px; }
  .contacts li {
    display: flex; align-items: center; gap: 8px;
    font-size: 13.5px; line-height: 1.45;
  }
  .contacts svg { width: 11px; height: 11px; flex: none; fill: var(--orange); }
  .card--back {
    display: flex; align-items: center; justify-content: center;
  }
  .brand--large { gap: 18px; }
  .brand--large .brand__mark { width: 92px; height: 92px; }
  .brand--large .brand__name { font-size: 44px; }
  .brand--large .brand__tagline { font-size: 13px; margin-top: 8px; }
</style>
</head>
<body>
  <section class="card card--front">
    <div class="portrait" role="img" aria-label="Porträtfoto des Inhabers mit Weste und verschränkten Armen vor grauem Hintergrund"></div>
    <div class="details">
      <div class="brand">
        <span class="brand__mark"></span>
        <div>
          <p class="brand__name">Leos Kellnerteam</p>
          <p class="brand__tagline">..weil jedes Fest gut bedient sein soll!</p>
        </div>
      </div>
      <h1 class="person__name">Leo Brandauer</h1>
      <p class="person__role">Inhaber</p>
      <p class="address">Lindenweg 12, 45100 Musterstadt</p>
      <ul class="contacts">
        <li><svg viewBox="0 0 24 24"><path d="M6.6 10.8a15 15 0 0 0 6.6 6.6l2.2-2.2a1 1 0 0 1 1-.25 11.4 11.4 0 0 0 3.6.57 1 1 0 0 1 1 1V20a1 1 0 0 1-1 1A17 17 0 0 1 3 4a1 1 0 0 1 1-1h3.5a1 1 0 0 1 1 1c0 1.25.2 2.45.57 3.57a1 1 0 0 1-.25 1z"/></svg>02300 555 01 23</li>
        <li><svg viewBox="0 0 24 24"><path d="M6.6 10.8a15 15 0 0 0 6.6 6.6l2.2-2.2a1 1 0 0 1 1-.25 11.4 11.4 0 0 0 3.6.57 1 1 0 0 1 1 1V20a1 1 0 0 1-1 1A17 17 0 0 1 3 4a1 1 0 0 1 1-1h3.5a1 1 0 0 1 1 1c0 1.25.2 2.45.57 3.57a1 1 0 0 1-.25 1z"/></svg>0170 555 47 19</li>
        <li><svg viewBox="0 0 24 24"><path d="M2 5h20v14H2z M2 5l10 8 10-8" stroke="#231f22" stroke-width="1.5"/></svg>info@leos-kellnerteam.de</li>
        <li><svg viewBox="0 0 24 24"><circle cx="12" cy="12" r="10"/><path d="M2 12h20M12 2c3 3 3 17 0 20M12 2c-3 3-3 17 0 20" stroke="#231f22" stroke-width="1.5" fill="none"/></svg>www.leos-kellnerteam.de</li>
        <li><svg viewBox="0 0 24 24"><circle cx="12" cy="12" r="10"/></svg>leos-kellnerteam</li>
      </ul>
    </div>
  </section>

  <section class="card card--back">
    <div class="brand brand--large">
      <span class="brand__mark"></span>
      <div>
        <p class="brand__name">Leos<br>Kellnerteam</p>
        <p class="brand__tagline">..weil jedes Fest gut bedient sein soll!</p>
      </div>
    </div>
  </section>
</body>
</html>
```